Quiet Harbor Prints gallery website

I need a Website for a gallery with a shopify integration or maybe even better also compatible with squarespace.
the website should have following riders: Künstler, Veranstaltungen, Shop, About Us.
some nice examples for inspiration of the website architecture are:
https://www.lindwerkraum.com/
https://www.plattenbau-salon.com/de/
https://moorlichtraum.de/
It should be easy for us to make adaptations and fill the website with new content.
Attached there is the CI an logo for the brand.
Target Market(s)
Art Collectors,
Industry/Entity Type
artgallery
Coding
Coded - Design and coding required
Number of Pages Required
3 page
Font styles to use
Look and feel

```html
<!DOCTYPE html>
<html lang="en">
<head>
<meta charset="utf-8">
<title>Quiet Harbor Prints</title>
<link href="https://fonts.googleapis.com/css2?family=Catamaran:wght@400;500&family=Poppins:wght@400;500&display=swap" rel="stylesheet">
<style>
:root{
  --red:#c4161c;
  --ink:#1b1b1b;
  --muted:#555;
  --paper:#ffffff;
  --mist:#ececee;
  --night:#0b0b0c;
  --line:#cfcfcf;
}
*{box-sizing:border-box;margin:0;padding:0}
html,body{width:1200px;height:4164px;overflow:hidden}
body{background:var(--paper);color:var(--ink);font-family:"Poppins",sans-serif;position:relative}
.abs{position:absolute}
section,header,footer{position:absolute;left:0;width:1200px}
.heading{font-family:"Catamaran",sans-serif;font-weight:400;text-transform:uppercase;letter-spacing:1px;color:var(--ink)}
.center{text-align:center;width:1200px;left:0}
.btn{display:flex;align-items:center;justify-content:center;background:var(--red);color:#fff;font-size:14px;font-weight:500;text-transform:uppercase}

/* header */
.site-header{top:0;height:188px;background:#f7f7f7}
.brand{top:18px;left:0;width:1200px;display:flex;flex-direction:column;align-items:center;gap:10px}
.brand-mark{width:30px;height:30px;border:2px solid var(--red)}
.brand-name{font-family:"Poppins",sans-serif;font-size:19px;font-weight:400;color:#333;letter-spacing:.5px}
.header-rule{top:137px;left:112px;width:976px;height:2px;background:var(--red)}
.main-nav{top:150px;left:112px;display:flex;gap:31px;font-size:14px;color:#333}
.tools{top:148px;left:918px;display:flex;gap:14px;align-items:center;font-size:14px;color:#222}
.tools svg{width:18px;height:18px;stroke:#222;fill:none;stroke-width:1.8}

/* hero */
.hero{top:188px;height:640px;background:linear-gradient(120deg,#4d5560 0%,#7b8894 30%,#5a6a7a 50%,#3d8fb0 65%,#c0477e 78%,#d9d9d9 100%)}
.hero-shade{top:0;left:0;width:1200px;height:640px;background:linear-gradient(90deg,rgba(0,0,0,.45),rgba(0,0,0,0) 60%)}
.hero-kicker{top:222px;left:112px;font-family:"Catamaran",sans-serif;font-size:27px;color:#fff;letter-spacing:.5px}
.hero-title{top:257px;left:108px;font-family:"Catamaran",sans-serif;font-size:54px;font-weight:500;color:#fff}
.hero-text{top:343px;left:112px;width:400px;font-size:14px;line-height:24px;color:#fff}

/* about */
.about{top:828px;height:553px}
.about-photo-a{top:86px;left:112px;width:252px;height:278px;background:linear-gradient(135deg,#4a2a1c,#b5562a 55%,#d98a3c)}
.about-frame{top:126px;left:230px;width:286px;height:340px;border:1.5px solid var(--red)}
.about-photo-b{top:170px;left:307px;width:265px;height:268px;background:linear-gradient(135deg,#2c2c2c,#8a8a8a 55%,#e5e5e5)}
.about-title{top:78px;left:597px;font-size:44px}
.about-text{top:140px;left:597px;width:490px;font-size:14.5px;line-height:24px;color:#444}
.about-text p+p{margin-top:24px}
.about-btn{top:352px;left:597px;width:112px;height:36px}

/* artists */
.artists{top:1381px;height:1040px;background:var(--mist)}
.artists-title{top:72px;font-size:43px}
.artist{width:294px}
.artist-photo{height:271px}
.artist-name{margin-top:5px;height:60px;border:2px solid var(--red);display:flex;align-items:center;justify-content:center;font-size:22px;font-weight:500;background:transparent}
.artists-btn{top:917px;left:543px;width:114px;height:36px}

/* events */
.events{top:2421px;height:802px}
.events-title{top:74px;font-size:47px}
.event{width:446px;height:210px}
.event-shadow{top:8px;left:8px;width:195px;height:202px;background:var(--red)}
.event-photo{top:0;left:0;width:195px;height:202px}
.event-card{top:0;left:195px;width:251px;height:189px;border:1.5px solid #999;border-left:none;background:#fff;padding:20px 0 0 26px}
.event-card h3{font-size:19px;font-weight:500;line-height:31px}
.event-card .desc{font-size:14px;line-height:22px;color:#444;margin-top:4px}
.event-meta{display:flex;align-items:center;gap:6px;font-size:14px;line-height:25px;color:#333}
.event-meta svg{width:12px;height:14px;fill:var(--red)}
.event-meta sup{font-size:8px}
.pager{top:3112px;left:0;width:1200px;display:flex;justify-content:center;gap:10px;align-items:center}
.pager span{width:27px;height:27px;background:#111;color:#fff;font-size:12px;display:flex;align-items:center;justify-content:center}
.pager i{font-style:normal;font-weight:600;letter-spacing:1px;color:#111}

/* shop */
.shop{top:3223px;height:642px;background:var(--mist)}
.shop-title{top:80px;font-size:45px}
.product{top:162px;width:223px}
.product-photo{height:221px}
.product-name{margin-top:10px;font-size:19px;font-weight:500;line-height:28px}
.product-link{margin-top:4px;display:inline-block;font-size:13px;color:var(--red);text-decoration:underline;text-transform:uppercase}
.arrow{top:240px;width:44px;height:44px;border-radius:50%;display:flex;align-items:center;justify-content:center}
.arrow svg{width:20px;height:20px;fill:none;stroke-width:2}
.arrow-prev{left:49px;border:2px solid #111}
.arrow-prev svg{stroke:#111}
.arrow-next{left:1107px;border:2px solid var(--red)}
.arrow-next svg{stroke:var(--red)}
.shop-btn{top:517px;left:543px;width:112px;height:37px}

/* footer */
.site-footer{top:3865px;height:299px;background:var(--night)}
.footer-brand{top:85px;left:0;width:1200px;display:flex;flex-direction:column;align-items:center;gap:12px}
.footer-brand .brand-mark{border-color:#fff;width:28px;height:28px}
.footer-brand .brand-name{color:#fff;font-size:17px}
.footer-nav{top:201px;left:0;width:1200px;display:flex;justify-content:center;gap:38px;font-size:17px;color:#fff}
.footer-rule{top:250px;left:112px;width:976px;height:1px;background:#444}
.copyright{top:268px;left:0;width:1200px;text-align:center;font-size:13px;color:#fff}
</style>
</head>
<body>

<header class="site-header">
  <div class="abs brand">
    <span class="brand-mark"></span>
    <span class="brand-name">QUIET HARBOR PRINTS</span>
  </div>
  <div class="abs header-rule"></div>
  <nav class="abs main-nav"><span>Artists</span><span>Events</span><span>Shop</span><span>About Us</span></nav>
  <div class="abs tools">
    <svg viewBox="0 0 20 20"><circle cx="10" cy="6" r="4"/><path d="M2 19c0-4 4-6 8-6s8 2 8 6"/></svg>
    <svg viewBox="0 0 20 20"><circle cx="8" cy="8" r="6"/><path d="M13 13l6 6"/></svg>
    <svg viewBox="0 0 20 20"><path d="M1 2h3l3 11h10l2-8H5"/><circle cx="8" cy="17" r="1.5" fill="#222"/><circle cx="16" cy="17" r="1.5" fill="#222"/></svg>
    <svg viewBox="0 0 20 20"><path d="M10 18S2 12 2 7a4 4 0 0 1 8-1 4 4 0 0 1 8 1c0 5-8 11-8 11z"/></svg>
    <span>EN&#8964;</span>
  </div>
</header>

<section class="hero">
  <div class="abs" role="img" aria-label="Artist painting a large colourful abstract canvas from above" style="top:0;left:0;width:1200px;height:640px"></div>
  <div class="abs hero-shade"></div>
  <div class="abs hero-kicker">WELCOME TO</div>
  <h1 class="abs hero-title">QUIET HARBOR PRINTS</h1>
  <p class="abs hero-text">Lorem ipsum dolor sit amet, consectetur adipiscing elit, sed do eiusmod tempor incididunt ut labore et dolore magna aliqua.</p>
</section>

<section class="about">
  <div class="abs about-photo-a" role="img" aria-label="Artist at work on a large warm-toned portrait painting"></div>
  <div class="abs about-frame"></div>
  <div class="abs about-photo-b" role="img" aria-label="Black and white ink wash artwork"></div>
  <h2 class="abs heading about-title">About Us</h2>
  <div class="abs about-text">
    <p>Lorem ipsum dolor sit amet, consectetur adipiscing elit, sed do eiusmod tempor incididunt ut labore et dolore magna aliqua. Quis ipsum suspendisse ultrices gravida. Risus commodo viver maecenas accumsan lacus vel facilisis.</p>
    <p>Lorem ipsum dolor sit amet, consectetur adipiscing elit, sed do eiusmod tempor incididunt ut labore et dolore magna aliqua. Quis ipsum suspendisse</p>
  </div>
  <a class="abs btn about-btn">Read More</a>
</section>

<section class="artists">
  <h2 class="abs heading center artists-title">Artists</h2>
  <div class="abs artist" style="top:167px;left:112px"><div class="artist-photo" role="img" aria-label="Brush applying red paint to canvas" style="background:linear-gradient(135deg,#dfe4ea,#9fb0c0 45%,#c4453a 60%,#2f3338)"></div><div class="artist-name">Lorem Ipsum</div></div>
  <div class="abs artist" style="top:167px;left:454px"><div class="artist-photo" role="img" aria-label="Figure in vivid body paint on dark blue" style="background:linear-gradient(135deg,#0f1c4a,#2a2f7a 50%,#c24a8a 75%,#e6a23a)"></div><div class="artist-name">Lorem Ipsum</div></div>
  <div class="abs artist" style="top:167px;left:796px"><div class="artist-photo" role="img" aria-label="Textured oil painting in pale and red tones" style="background:linear-gradient(160deg,#efe5df,#d9b3a6 50%,#c8393a 80%,#e8d9d2)"></div><div class="artist-name">Lorem Ipsum</div></div>
  <div class="abs artist" style="top:543px;left:112px"><div class="artist-photo" role="img" aria-label="Colourful paint splash artwork" style="background:radial-gradient(circle at 50% 45%,#f4d03f,#e74c8b 30%,#3aa0d8 55%,#cfcac0 80%)"></div><div class="artist-name">Lorem Ipsum</div></div>
  <div class="abs artist" style="top:543px;left:454px"><div class="artist-photo" role="img" aria-label="Impressionist cityscape painting in purple and orange" style="background:linear-gradient(135deg,#6a3fd0,#4c5fe0 40%,#e07a2a 70%,#3a3fa8)"></div><div class="artist-name">Lorem Ipsum</div></div>
  <div class="abs artist" style="top:543px;left:796px"><div class="artist-photo" role="img" aria-label="Cubist mosaic painting in red, yellow and teal" style="background:linear-gradient(135deg,#b0302a,#e2a93a 35%,#2f7f86 65%,#6b2a1f)"></div><div class="artist-name">Lorem Ipsum</div></div>
  <a class="abs btn artists-btn">View More</a>
</section>

<section class="events">
  <h2 class="abs heading center events-title">Upcoming Event</h2>

  <article class="abs event" style="top:160px;left:112px">
    <div class="abs event-shadow"></div>
    <div class="abs event-photo" role="img" aria-label="Gallery room with a large abstract painting" style="background:linear-gradient(135deg,#2b4a5c,#c8582e 45%,#e8ddd0)"></div>
    <div class="abs event-card"><h3>Lorem ipsum dolor<br>sit amet,</h3><p class="desc">Lorem ipsum dolor sit<br>amet, consectetur</p>
      <div class="event-meta"><svg viewBox="0 0 12 14"><path d="M6 0a5 5 0 0 1 5 5c0 4-5 9-5 9S1 9 1 5a5 5 0 0 1 5-5z"/></svg>Lorem Ipsum</div>
      <div class="event-meta"><svg viewBox="0 0 12 14"><rect x="0" y="2" width="12" height="12" rx="1"/></svg>09<sup>th</sup> Feb 2024</div></div>
  </article>

  <article class="abs event" style="top:160px;left:642px">
    <div class="abs event-shadow"></div>
    <div class="abs event-photo" role="img" aria-label="Visitors viewing classical paintings in a museum" style="background:linear-gradient(135deg,#5a4a3a,#8c7b62 45%,#2e3440)"></div>
    <div class="abs event-card"><h3>Lorem ipsum dolor<br>sit amet,</h3><p class="desc">Lorem ipsum dolor sit<br>amet, consectetur</p>
      <div class="event-meta"><svg viewBox="0 0 12 14"><path d="M6 0a5 5 0 0 1 5 5c0 4-5 9-5 9S1 9 1 5a5 5 0 0 1 5-5z"/></svg>Lorem Ipsum</div>
      <div class="event-meta"><svg viewBox="0 0 12 14"><rect x="0" y="2" width="12" height="12" rx="1"/></svg>09<sup>th</sup> Feb 2024</div></div>
  </article>

  <article class="abs event" style="top:417px;left:112px">
    <div class="abs event-shadow"></div>
    <div class="abs event-photo" role="img" aria-label="Dim exhibition hall with visitors" style="background:linear-gradient(135deg,#1e1a16,#6b4a2c 50%,#2a2420)"></div>
    <div class="abs event-card"><h3>Lorem ipsum dolor<br>sit amet,</h3><p class="desc">Lorem ipsum dolor sit<br>amet, consectetur</p>
      <div class="event-meta"><svg viewBox="0 0 12 14"><path d="M6 0a5 5 0 0 1 5 5c0 4-5 9-5 9S1 9 1 5a5 5 0 0 1 5-5z"/></svg>Lorem Ipsum</div>
      <div class="event-meta"><svg viewBox="0 0 12 14"><rect x="0" y="2" width="12" height="12" rx="1"/></svg>09<sup>th</sup> Feb 2024</div></div>
  </article>

  <article class="abs event" style="top:417px;left:642px">
    <div class="abs event-shadow"></div>
    <div class="abs event-photo" role="img" aria-label="Painters working at easels in a bright studio" style="background:linear-gradient(135deg,#e8e0d4,#b08a66 45%,#5c4a3c)"></div>
    <div class="abs event-card"><h3>Lorem ipsum dolor<br>sit amet,</h3><p class="desc">Lorem ipsum dolor sit<br>amet, consectetur</p>
      <div class="event-meta"><svg viewBox="0 0 12 14"><path d="M6 0a5 5 0 0 1 5 5c0 4-5 9-5 9S1 9 1 5a5 5 0 0 1 5-5z"/></svg>Lorem Ipsum</div>
      <div class="event-meta"><svg viewBox="0 0 12 14"><rect x="0" y="2" width="12" height="12" rx="1"/></svg>09<sup>th</sup> Feb 2024</div></div>
  </article>
</section>
<nav class="abs pager"><span>01</span><span>02</span><span>03</span><i>····</i><span>09</span></nav>

<section class="shop">
  <h2 class="abs heading center shop-title">Online Shop</h2>
  <div class="abs arrow arrow-prev"><svg viewBox="0 0 20 20"><path d="M13 3L6 10l7 7"/></svg></div>
  <div class="abs arrow arrow-next"><svg viewBox="0 0 20 20"><path d="M7 3l7 7-7 7"/></svg></div>
  <div class="abs product" style="left:112px"><div class="product-photo" role="img" aria-label="Fantasy painting with a blue and orange sky" style="background:linear-gradient(180deg,#1d3a8a,#d8622a 45%,#2f8fd0 75%,#f0c040)"></div><div class="product-name">Lorem ipsum dolor sit amet,</div><a class="product-link">Click Here</a></div>
  <div class="abs product" style="left:362px"><div class="product-photo" role="img" aria-label="Golden devotional painting" style="background:linear-gradient(135deg,#3a2a14,#b07a2a 50%,#4a3a1c)"></div><div class="product-name">Lorem ipsum dolor sit amet,</div><a class="product-link">Click Here</a></div>
  <div class="abs product" style="left:614px"><div class="product-photo" role="img" aria-label="Traditional procession painting in grey and red" style="background:linear-gradient(135deg,#8a8f90,#a04048 50%,#6a6f72)"></div><div class="product-name">Lorem ipsum dolor sit amet,</div><a class="product-link">Click Here</a></div>
  <div class="abs product" style="left:865px"><div class="product-photo" role="img" aria-label="Colourful abstract painting in blue and orange" style="background:radial-gradient(circle,#111 12%,#1d6fb0 28%,#e07a2a 55%,#d8d4cf 85%)"></div><div class="product-name">Lorem ipsum dolor sit amet,</div><a class="product-link">Click Here</a></div>
  <a class="abs btn shop-btn">View More</a>
</section>

<footer class="site-footer">
  <div class="abs footer-brand">
    <span class="brand-mark"></span>
    <span class="brand-name">QUIET HARBOR PRINTS</span>
  </div>
  <nav class="abs footer-nav"><span>Artists</span><span>Events</span><span>Shop</span><span>About Us</span><span>Contact Us</span></nav>
  <div class="abs footer-rule"></div>
  <p class="abs copyright">© 2023 Quiet Harbor Prints, All Rights Reserved</p>
</footer>

</body>
</html>
```